New, modern business card for growing audiology practice

We need a new business card for our audiology practice. Our logo and website have recently changed (more modern) and we want our business cards to reflect this change.
We conduct hearing tests, perform earwax removals, and fit & dispense hearing aids to our patients. We are a family owned practice in which the owner is the one who works directly with the patient. I have attached logos in various formats to use, as well as two ideas I found on this website; as well as a scanned copy of our current logo. Good luck!

Industry/Entity Type

Business

Contact Information for Business Card

Company name: Tolvera Hearing Center
Provider name: Peter Wolstenby, Au.D. F/NSB
Phone number: (440) 683-5127
Address: 837 W. Lindell Ave. Brennock Falls, OH 44198
email: tolverahearing@postvane.com
website: tolverahearing.com

Colors
000000
aaaaaa
dbdbdb
cacaca
9bcb3c
afd23c
cadf82
b1b1b1

Requirements
Must have
• My card must include information in the "details" section. In the attached images, I found a few that I liked and I would like to model after - "brisky bouncin'" and "Sound Method Center".
• Must be horizontal.
• Must include logos provided. I uploaded them in various file formats and various ways.
• Must match logo font, if possible, if not, please get as close as you can.
Nice to have
• I really like the idea of having a color on one side with just the logo and company name and the contact information and provider name on the other side. I also really like the idea of having the main color dominating on the logo/company side with accent of that same color on the contact side of the card.
Should not have
• Must not be vertical.

```html
<!DOCTYPE html>
<html lang="en">
<head>
<meta charset="utf-8">
<title>Tolvera Hearing Center – Business Card</title>
<link rel="stylesheet" href="https://fonts.googleapis.com/css2?family=Cabin:wght@500&family=Dosis:wght@600&family=Roboto:wght@400&display=swap">
<style>
  :root {
    --page-bg: #e4e4e4;
    --brand-green: #5b9436;
    --brand-green-dark: #4f8530;
    --accent-green: #5f9a3a;
    --card-white: #f4f4f4;
    --ink: #111111;
    --ink-soft: #222222;
    --on-green: #ffffff;
  }
  * { margin: 0; padding: 0; box-sizing: border-box; }
  html, body { width: 1200px; height: 576px; overflow: hidden; }
  body {
    background: var(--page-bg);
    position: relative;
    font-family: "Roboto", Arial, sans-serif;
  }
  .card {
    position: absolute;
    top: 139px;
    width: 484px;
    height: 292px;
    border-radius: 12px;
    overflow: hidden;
  }
  .card--front {
    left: 82px;
    background: linear-gradient(160deg, var(--brand-green) 0%, var(--brand-green-dark) 100%);
  }
  .card--back {
    left: 602px;
    background: var(--card-white);
  }
  .wordmark {
    font-family: "Cabin", "Gill Sans", sans-serif;
    font-weight: 500;
    text-transform: uppercase;
    line-height: 1;
  }
  .wordmark__line { display: block; white-space: nowrap; }
  .front-brand {
    position: absolute;
    left: 112px;
    top: 115px;
    display: flex;
    align-items: center;
    gap: 28px;
  }
  .front-brand__dot {
    width: 40px;
    height: 40px;
    border-radius: 50%;
    background: var(--on-green);
    flex: none;
  }
  .front-brand .wordmark { color: var(--on-green); }
  .front-brand .wordmark__line--top { font-size: 43px; }
  .front-brand .wordmark__line--bottom { font-size: 24px; margin-top: 4px; }
  .back-brand {
    position: absolute;
    left: 28px;
    top: 30px;
  }
  .back-brand .wordmark { color: var(--ink); }
  .back-brand .wordmark__line--top { font-size: 33px; }
  .back-brand .wordmark__line--bottom { font-size: 18px; margin-top: 3px; }
  .provider {
    position: absolute;
    left: 28px;
    top: 128px;
  }
  .provider__name {
    font-family: "Dosis", "Arial Narrow", sans-serif;
    font-weight: 600;
    font-size: 20px;
    color: var(--accent-green);
  }
  .provider__role {
    margin-top: 5px;
    font-size: 12px;
    color: var(--ink-soft);
  }
  .contact-list {
    position: absolute;
    left: 28px;
    top: 183px;
    list-style: none;
    font-size: 12.5px;
    color: var(--ink-soft);
    line-height: 17px;
  }
  .contact-list li {
    display: flex;
    align-items: flex-start;
  }
  .contact-list .icon {
    width: 10px;
    height: 10px;
    margin-top: 3.5px;
    margin-right: 10px;
    flex: none;
    fill: var(--accent-green);
  }
</style>
</head>
<body>
  <section class="card card--front" aria-label="Card front">
    <div class="front-brand">
      <span class="front-brand__dot"></span>
      <div class="wordmark">
        <span class="wordmark__line wordmark__line--top">Tolvera</span>
        <span class="wordmark__line wordmark__line--bottom">Hearing Center</span>
      </div>
    </div>
  </section>

  <section class="card card--back" aria-label="Card back">
    <div class="back-brand">
      <div class="wordmark">
        <span class="wordmark__line wordmark__line--top">Tolvera</span>
        <span class="wordmark__line wordmark__line--bottom">Hearing Center</span>
      </div>
    </div>

    <div class="provider">
      <p class="provider__name">Peter Wolstenby, Au.D. F/NSB</p>
      <p class="provider__role">Owner - Audiologist</p>
    </div>

    <ul class="contact-list">
      <li>
        <svg class="icon" viewBox="0 0 10 10" aria-hidden="true"><path d="M5 0a3.6 3.6 0 0 0-3.6 3.6C1.4 6.3 5 10 5 10s3.6-3.7 3.6-6.4A3.6 3.6 0 0 0 5 0zm0 5a1.4 1.4 0 1 1 0-2.8A1.4 1.4 0 0 1 5 5z"/></svg>
        <span>837 W. Lindell Ave.<br>Brennock Falls, OH 44198</span>
      </li>
      <li>
        <svg class="icon" viewBox="0 0 10 10" aria-hidden="true"><path d="M0 3.2C0 1.6 2 .8 5 .8s5 .8 5 2.4v.8H7.2V2.9H2.8V4H0z M2.4 4.6h5.2L9.4 9.2H.6z"/></svg>
        <span>(440) 683-5127</span>
      </li>
      <li>
        <svg class="icon" viewBox="0 0 10 10" aria-hidden="true"><path d="M0 1.6h10v.8L5 5.6 0 2.4z M0 3.6l5 3.2 5-3.2v4.8H0z"/></svg>
        <span>tolverahearing@postvane.com</span>
      </li>
      <li>
        <svg class="icon" viewBox="0 0 10 10" aria-hidden="true"><circle cx="5" cy="5" r="4.6"/><path d="M.4 5h9.2M5 .4c-2.4 2.6-2.4 6.6 0 9.2M5 .4c2.4 2.6 2.4 6.6 0 9.2" stroke="#f4f4f4" stroke-width=".7" fill="none"/></svg>
        <span>www.tolverahearing.com</span>
      </li>
    </ul>
  </section>
</body>
</html>
```